Personal training and nutrition business needs business card design

We need a business card that outlays our services and invites potential customers to join our team and take the first step to a healthier and more enjoyable life. We cater for any level of fitness and specialize in weight loss and conditioning, strength training, muscle gain and strength endurance. Whether you are just starting off or need some help getting to the next level of your journey we are here to get the job done.
We specialize in one on one or one on two personal training sessions and each program will be custom made to suit individual fitness goals of our clients

```html
<!DOCTYPE html>
<html lang="en">
<head>
<meta charset="utf-8">
<title>Stride &amp; Steel – Business Card</title>
<link rel="stylesheet" href="https://fonts.googleapis.com/css2?family=Montserrat:wght@400;500;600;800&display=swap">
<style>
  :root {
    --bg: #d6d6d6;
    --purple-light: #b262ad;
    --purple-deep: #6c45a0;
    --purple-text: #8a4fb0;
    --ink: #1a1a1a;
    --white: #ffffff;
    --card-shadow: 0 10px 24px rgba(0,0,0,0.28);
  }
  * { box-sizing: border-box; margin: 0; padding: 0; }
  html, body { width: 1200px; height: 900px; overflow: hidden; }
  body {
    background: var(--bg);
    font-family: "Montserrat", Arial, sans-serif;
    position: relative;
  }
  .card {
    position: absolute;
    width: 540px;
    height: 310px;
    border-radius: 26px;
    box-shadow: var(--card-shadow);
    overflow: hidden;
  }
  /* front */
  .card-front {
    left: 70px; top: 110px;
    background: linear-gradient(150deg, var(--purple-light) 0%, #8d55a8 45%, var(--purple-deep) 100%);
    color: var(--white);
    display: flex;
    flex-direction: column;
    align-items: center;
    justify-content: center;
    text-align: center;
  }
  .brand { display: flex; align-items: center; gap: 14px; }
  .brand-dot { width: 22px; height: 22px; border-radius: 50%; flex: none; }
  .card-front .brand-dot { background: var(--white); }
  .brand-name {
    font-weight: 800;
    font-size: 38px;
    letter-spacing: 1px;
    line-height: 1;
    text-transform: uppercase;
    white-space: nowrap;
  }
  .tagline {
    font-weight: 600;
    font-size: 9px;
    letter-spacing: 1.5px;
    text-transform: uppercase;
    margin-top: 10px;
  }
  .services {
    margin-top: 34px;
    font-size: 15px;
    line-height: 1.45;
    font-weight: 400;
  }
  /* back */
  .card-back {
    left: 590px; top: 480px;
    background: linear-gradient(120deg, var(--white) 55%, #eeeeee 100%);
    color: var(--ink);
  }
  .back-brand { position: absolute; left: 40px; top: 46px; }
  .card-back .brand-dot { background: var(--purple-text); }
  .card-back .brand-name { font-size: 30px; color: var(--ink); }
  .card-back .tagline { color: var(--purple-text); margin-left: 36px; margin-top: 8px; }
  .person { position: absolute; left: 40px; top: 140px; }
  .person-name {
    color: var(--purple-text);
    font-size: 22px;
    font-weight: 500;
    letter-spacing: 0.5px;
    text-transform: uppercase;
    white-space: nowrap;
  }
  .person-role { font-size: 14px; margin-top: 2px; }
  .contacts { position: absolute; left: 40px; top: 212px; list-style: none; font-size: 14px; }
  .contacts li { display: flex; align-items: center; gap: 9px; line-height: 24px; white-space: nowrap; }
  .contacts svg { width: 15px; height: 15px; fill: var(--purple-text); flex: none; }
  .contacts .accent { color: var(--purple-text); }
  .address {
    position: absolute; right: 34px; top: 150px;
    text-align: right; font-size: 14px; line-height: 1.4;
    white-space: nowrap;
  }
</style>
</head>
<body>
  <section class="card card-front" aria-label="Card front">
    <div class="brand">
      <span class="brand-dot"></span>
      <span class="brand-name">Stride &amp; Steel</span>
    </div>
    <p class="tagline">Personal Training. Nutrition. Motivation</p>
    <p class="services">
      Weight loss &amp; Conditioning • Strength Training<br>
      Muscle Gain • Strength Endurance
    </p>
  </section>

  <section class="card card-back" aria-label="Card back">
    <div class="back-brand">
      <div class="brand">
        <span class="brand-dot"></span>
        <span class="brand-name">Stride &amp; Steel</span>
      </div>
      <p class="tagline">Personal Training. Nutrition. Motivation</p>
    </div>

    <div class="person">
      <p class="person-name">Marcus Reed</p>
      <p class="person-role">Managing Director</p>
    </div>

    <ul class="contacts">
      <li>
        <svg viewBox="0 0 24 24" aria-hidden="true"><path d="M6.6 10.8a15.1 15.1 0 0 0 6.6 6.6l2.2-2.2a1 1 0 0 1 1-.25 11.4 11.4 0 0 0 3.6.57 1 1 0 0 1 1 1V20a1 1 0 0 1-1 1A17 17 0 0 1 3 4a1 1 0 0 1 1-1h3.5a1 1 0 0 1 1 1c0 1.25.2 2.450.57 3.57a1 1 0 0 1-.25 1z"/></svg>
        044-555 210 384
      </li>
      <li>
        <svg viewBox="0 0 24 24" aria-hidden="true"><path d="M2 5h20v14H2zm2 2v.4l8 5 8-5V7zm0 2.7V17h16V9.7l-8 5z"/></svg>
        hello@stridesteel.com
      </li>
      <li>
        <svg viewBox="0 0 24 24" aria-hidden="true"><path d="M12 2a10 10 0 1 0 0 20 10 10 0 0 0 0-20zm6.9 9h-3a15 15 0 0 0-1.3-5.6A8 8 0 0 1 18.9 11zM12 4.1c.9 1.2 1.8 3.6 1.900 6.9h-3.8c.1-3.3 1-5.7 1.9-6.9zM9.4 5.4A15 15 0 0 0 8.1 11h-3a8 8 0 0 1 4.3-5.6zM5.1 13h3a15 15 0 0 0 1.3 5.6A8 8 0 0 1 5.1 13zm6.9 6.9c-.9-1.2-1.8-3.6-1.9-6.9h3.8c-.1 3.3-1 5.7-1.9 6.9zm2.6-1.3a15 15 0 0 0 1.3-5.6h3a8 8 0 0 1-4.3 5.6z"/></svg>
        <span>www.<span class="accent">stridesteel</span>.com</span>
      </li>
    </ul>

    <p class="address">18 Harbour Lane, Suite 4<br>30217, Eastvale</p>
  </section>
</body>
</html>
```